Professional Package for CPA Firm

We would like a stationery design for our new CPA Firm based in Atlanta, GA called 'Vale 8'. We work with investors to help grow investments, tax free. We would like the design to have a professional/minimal look with a 'wow' factor. We need 9.5″ x 4.125″, 9x12, and 10x13 mailing envelopes, business cards, and a letterhead. We have a logo that is already complete. For the letterhead, we would like to have space to put credentials at the bottom of the page

Industry/Entity Type

CPA, Accounting

```html
<!DOCTYPE html>
<html lang="en">
<head>
<meta charset="utf-8">
<title>Vale 8 — Stationery Set</title>
<link href="https://fonts.googleapis.com/css2?family=Montserrat:wght@400;500;700;800&family=Open+Sans:wght@400;600;700&display=swap" rel="stylesheet">
<style>
  :root{
    --backdrop:#e5e5e5;
    --paper:#efefef;
    --paper-edge:#dcdcdc;
    --ink:#1c1c1e;
    --body-ink:#3d3d3f;
    --muted:#5a5a5c;
    --brand-blue:#2a97cf;
    --flap-black:#18191b;
    --card-dark:#2e2f31;
  }
  *{box-sizing:border-box;margin:0;padding:0}
  html,body{width:1200px;height:795px;overflow:hidden;background:var(--backdrop)}
  body{position:relative;font-family:"Open Sans",Arial,sans-serif;color:var(--body-ink)}
  .sheet{position:absolute;background:var(--paper);border:1px solid var(--paper-edge)}

  .wordmark{font-family:"Montserrat",Arial,sans-serif;font-weight:800;color:var(--ink);letter-spacing:.5px;line-height:1;display:flex;align-items:center;gap:.3em}
  .wordmark .mark-dot{display:inline-block;width:.55em;height:.55em;border-radius:50%;background:var(--brand-blue)}
  .tagline{font-family:"Montserrat",Arial,sans-serif;font-weight:500;color:var(--ink);letter-spacing:.8px;line-height:1}

  /* Letterhead */
  .letterhead{left:292px;top:99px;width:294px;height:415px}
  .letterhead .brand{position:absolute;top:58px;left:0;right:0;display:flex;flex-direction:column;align-items:center;gap:4px}
  .letterhead .wordmark{font-size:17px}
  .letterhead .tagline{font-size:5.2px}
  .letter-body{position:absolute;left:27px;top:97px;width:241px;font-size:5.4px;line-height:8px;text-align:justify}
  .letter-body p{margin-bottom:8px}
  .letter-footer{position:absolute;left:0;right:0;top:380px;text-align:center;font-size:6px;line-height:9px;color:var(--muted)}
  .letter-footer .contacts{display:flex;justify-content:center;gap:5px;align-items:center}
  .letter-footer svg{width:6px;height:6px;vertical-align:-1px;margin-right:2px}

  /* Presentation folder */
  .folder{left:637px;top:80px;width:346px;height:437px}
  .folder .spine{position:absolute;left:3px;top:0;bottom:0;width:17px;border-left:1px solid var(--paper-edge);border-right:1px solid var(--paper-edge)}
  .folder .brand{position:absolute;top:80px;left:0;right:0;display:flex;flex-direction:column;align-items:center;gap:5px}
  .folder .wordmark{font-size:22px}
  .folder .tagline{font-size:6.6px}
  .folder-photo{position:absolute;left:0;right:0;top:137px;height:232px;background:linear-gradient(115deg,#4a4d52 0%,#b9c0c4 35%,#d8d4cc 55%,#8fa3ad 78%,#2a8fc4 100%)}
  .folder-url{position:absolute;left:0;right:0;top:397px;text-align:center;font-family:"Montserrat",Arial,sans-serif;font-size:9.4px;letter-spacing:1.6px;color:var(--body-ink)}
  .folder-url .accent{color:var(--brand-blue)}

  /* Business cards */
  .card-front{left:187px;top:551px;width:132px;height:74px}
  .card-front .brand{position:absolute;left:18px;top:28px;display:flex;flex-direction:column;gap:3px}
  .card-front .wordmark{font-size:9px}
  .card-front .tagline{font-size:2.6px;letter-spacing:.3px}
  .card-front .divider{position:absolute;left:62px;top:20px;width:1px;height:34px;background:var(--brand-blue)}
  .card-front .details{position:absolute;left:69px;top:20px;font-size:3.3px;line-height:4.3px;color:var(--ink)}
  .card-front .name{font-weight:700;font-size:4.2px;line-height:4.6px}
  .card-front .role{font-weight:600;margin-bottom:2px}
  .card-back{left:187px;top:646px;width:132px;height:75px;border:none;background:linear-gradient(135deg,#3a3b3d,var(--card-dark) 60%,#232426)}

  /* Envelopes */
  .envelope-front{left:353px;top:561px;width:329px;height:157px}
  .envelope-front .brand{position:absolute;left:32px;top:56px;display:flex;flex-direction:column;align-items:center;gap:3px}
  .envelope-front .wordmark{font-size:13px}
  .envelope-front .tagline{font-size:4px}
  .envelope-front .return-address{margin-top:3px;text-align:center;font-size:5.4px;line-height:7px;color:var(--muted)}
  .envelope-back{left:713px;top:561px;width:329px;height:157px}
  .envelope-back svg.flap{position:absolute;left:-1px;top:-1px}
  .envelope-back .brand{position:absolute;left:0;right:0;top:30px;display:flex;flex-direction:column;align-items:center;gap:2px}
  .envelope-back .wordmark{font-size:8px;color:#fff}
  .envelope-back .tagline{font-size:2.4px;color:#cfcfcf;letter-spacing:.3px}
</style>
</head>
<body>

<section class="sheet letterhead" aria-label="Letterhead">
  <div class="brand">
    <div class="wordmark">Vale 8</div>
    <div class="tagline">CPAs and Tax Advisors</div>
  </div>
  <div class="letter-body">
    <p>Dear customer,</p>
    <p>Lorem ipsum dolor sit amet, consectetur adipisicing elit, sed do eiusmod tempor incididunt ut labore et dolore magna aliqua. Ut enim ad minim veniam, quis nostrud exercitation ullamco laboris nisi ut aliquip ex ea commodo consequat. Duis aute irure dolor in reprehenderit in voluptate velit esse cillum dolore eu fugiat nulla pariatur. Excepteur sint occaecat cupidatat non proident, sunt in culpa qui officia deserunt mollit anim id est laborum.</p>
    <p>Lorem ipsum dolor sit amet, consectetur adipisicing elit, sed do eiusmod tempor incididunt ut labore et dolore magna aliqua. Ut enim ad minim veniam, quis nostrud exercitation ullamco laboris nisi ut aliquip ex ea commodo consequat. Duis aute irure dolor in reprehenderit in voluptate velit esse cillum dolore eu fugiat nulla pariatur. Excepteur sint occaecat cupidatat non proident, sunt in culpa qui officia deserunt mollit anim id est laborum.</p>
    <p>Lorem ipsum dolor sit amet, consectetur adipisicing elit, sed do eiusmod tempor incididunt ut labore et dolore magna aliqua. Ut enim ad minim veniam, quis nostrud exercitation ullamco laboris nisi ut aliquip ex ea commodo consequat. Duis aute irure dolor in reprehenderit in voluptate velit esse cillum dolore eu fugiat nulla pariatur. Excepteur sint occaecat cupidatat non proident, sunt in culpa qui officia deserunt mollit anim id est laborum.</p>
    <p>Lorem ipsum dolor sit amet, consectetur adipisicing elit, sed do eiusmod tempor incididunt ut labore et dolore magna aliqua. Ut enim ad minim veniam, quis nostrud exercitation ullamco laboris nisi ut aliquip ex ea commodo consequat. Duis aute irure dolor in reprehenderit.</p>
    <p>Yours Sincerely,</p>
  </div>
  <footer class="letter-footer">
    <div>48 Harbor Ridge Lane, Marietta, GA 30062</div>
    <div class="contacts">
      <span><svg viewBox="0 0 10 10"><path d="M2 1l2 0 1 2.5-1.2 1a5 5 0 0 0 2.7 2.7l1-1.2L9 7v2c-4.5 0-8-3.5-8-8z" fill="#1c1c1e"/></svg>+14045550187</span>
      <span><svg viewBox="0 0 10 10"><rect x="0.5" y="2" width="9" height="6.5" fill="#1c1c1e"/><path d="M0.8 2.3L5 5.5l4.2-3.2" stroke="#efefef" stroke-width=".9" fill="none"/></svg>info@valeeight.com</span>
      <span><svg viewBox="0 0 10 10"><circle cx="5" cy="5" r="4" fill="none" stroke="#1c1c1e" stroke-width="1"/><path d="M1 5h8M5 1c-2 2.5-2 5.5 0 8M5 1c2 2.5 2 5.5 0 8" stroke="#1c1c1e" stroke-width=".8" fill="none"/></svg>www.valeeight.com</span>
    </div>
  </footer>
</section>

<section class="sheet folder" aria-label="Presentation folder">
  <div class="spine"></div>
  <div class="brand">
    <div class="wordmark">Vale 8</div>
    <div class="tagline">CPAs and Tax Advisors</div>
  </div>
  <div class="folder-photo" role="img" aria-label="Photo of two advisors reviewing a laptop in a bright office, with dark and blue angled overlays"></div>
  <div class="folder-url">www.<span class="accent">valeeight</span>.com</div>
</section>

<section class="sheet card-front" aria-label="Business card front">
  <div class="brand">
    <div class="wordmark">Vale 8</div>
    <div class="tagline">CPAs and Tax Advisors</div>
  </div>
  <div class="divider"></div>
  <div class="details">
    <div class="name">DANIEL MORROW</div>
    <div class="role">Managing Director</div>
    <div>48 Harbor Ridge Lane,</div>
    <div>Marietta, GA 30062</div>
    <div>+14045550187</div>
    <div>info@valeeight.com</div>
    <div>www.valeeight.com</div>
  </div>
</section>

<section class="sheet card-back" role="img" aria-label="Business card back with a dark repeating decorative pattern"></section>

<section class="sheet envelope-front" aria-label="Envelope front">
  <div class="brand">
    <div class="wordmark">Vale 8</div>
    <div class="tagline">CPAs and Tax Advisors</div>
    <div class="return-address">48 Harbor Ridge Lane,<br>Marietta, GA 30062</div>
  </div>
</section>

<section class="sheet envelope-back" aria-label="Envelope back">
  <svg class="flap" width="329" height="52" viewBox="0 0 329 52">
    <polygon points="0,0 329,0 324,50 7,50" fill="var(--flap-black)"/>
  </svg>
  <div class="brand">
    <div class="wordmark">Vale 8</div>
    <div class="tagline">CPAs and Tax Advisors</div>
  </div>
</section>

</body>
</html>
```